Help our Sugar Loom find our winning design! We're looking for a business card....

We’re a Sugar Loom in NY specializing in custom-made cakes and unique desserts.
Our cakes combine flavor and art, each designed to match customer’s special event and theme.
We’d like a unique business card with a clean design that will combine French chic and artistic look & feel.
We’d like to differentiate ourselves from standard bakeries, please don’t offer cupcake images :-)
Our logo is peach-pink and brown and we’d love to use these colors ( . Another color that can be added is gold - or feel free to suggest!

Target Market(s)

Women, ages 25-55

Industry/Entity Type

Boutique

Contact Information for Business Card

Text on card:
Logo
Sugar Loom by Dana Welch

www.sugarloomsweets.com
hello@sugarloom.com
(516) 555-0147
F – sugarloomnyc
IG - sugarloom_ny

Font styles to use
Sans Serif
Script

Requirements
Must have
• Logo
• Clean look
• French chic and artistic look & feel.
Nice to have
• Damask pattern
Should not have
• Cupcake images

```html
<!DOCTYPE html>
<html lang="en">
<head>
<meta charset="utf-8">
<title>Sugar Loom business card</title>
<link rel="stylesheet" href="https://fonts.googleapis.com/css2?family=Open+Sans:wght@400;600&display=swap">
<style>
  :root {
    --backdrop: #e9e6e3;
    --cocoa: #3d2b26;
    --cocoa-deep: #2f211d;
    --peach: #e6a28f;
    --peach-soft: #f3d3c8;
    --paper: #ffffff;
    --ink: #3a2a25;
  }
  * { box-sizing: border-box; margin: 0; padding: 0; }
  html, body { width: 1200px; height: 900px; overflow: hidden; }
  body {
    background: var(--backdrop);
    font-family: "Open Sans", Arial, sans-serif;
    position: relative;
  }
  .card {
    position: absolute;
    left: 250px;
    width: 700px;
    height: 400px;
    box-shadow: 0 6px 22px rgba(0,0,0,.18);
    overflow: hidden;
  }
  .card--front { top: 35px; background: var(--cocoa); }
  .card--back { top: 465px; background: var(--paper); }
  .card__frame { position: absolute; inset: 0; }
  .logo-ornament {
    position: absolute;
    left: 110px; top: 60px;
    width: 480px; height: 170px;
    border-radius: 50% / 40%;
  }
  .card--front .logo-ornament {
    background: radial-gradient(ellipse at center, rgba(230,162,143,.22), rgba(230,162,143,.04) 70%, transparent 75%);
  }
  .card--back .logo-ornament {
    background: radial-gradient(ellipse at center, rgba(230,162,143,.25), rgba(230,162,143,.05) 70%, transparent 75%);
  }
  .brand-name {
    position: absolute;
    left: 0; right: 0; top: 128px;
    text-align: center;
    font-size: 46px;
    font-weight: 400;
    letter-spacing: 1px;
  }
  .card--front .brand-name { color: #f4ece8; }
  .card--back .brand-name { color: var(--ink); }
  .tagline {
    position: absolute;
    left: 0; right: 0; top: 208px;
    text-align: center;
    font-size: 15px;
    letter-spacing: 6px;
    color: var(--peach);
  }
  .card--back .tagline { color: var(--ink); }
  .owner-line {
    position: absolute;
    left: 0; right: 0; top: 252px;
    display: flex; justify-content: center; align-items: center; gap: 14px;
    font-size: 14px;
    color: var(--peach-soft);
  }
  .owner-line__flag { width: 22px; height: 16px; }
  .contacts {
    position: absolute;
    left: 40px; right: 40px; top: 290px;
    display: flex; flex-direction: column; align-items: center; gap: 8px;
    font-size: 16px;
    color: var(--ink);
  }
  .contacts__row { display: flex; gap: 22px; align-items: center; }
  .contact { display: flex; align-items: center; gap: 6px; }
  .contact__icon { width: 15px; height: 15px; flex: none; }
  .contact__square { width: 13px; height: 13px; background: var(--peach); flex: none; }
</style>
</head>
<body>

<section class="card card--front" aria-label="Card front">
  <svg class="card__frame" width="700" height="400" viewBox="0 0 700 400" aria-hidden="true">
    <path d="M42 20 H658 A22 22 0 0 0 680 42 V358 A22 22 0 0 0 658 380 H42 A22 22 0 0 0 20 358 V42 A22 22 0 0 0 42 20 Z"
          fill="none" stroke="#e6a28f" stroke-width="1.5"/>
  </svg>
  <div class="logo-ornament" role="img" aria-label="Peach flourish ornament with a tiered cake motif framing the brand name"></div>
  <div class="brand-name">Sugar Loom</div>
  <div class="tagline">HANDCRAFTED WITH LOVE</div>
  <div class="owner-line">
    <svg class="owner-line__flag" viewBox="0 0 22 16" aria-hidden="true"><path d="M0 0 H22 V16 H0 L6 8 Z" fill="#e6a28f"/></svg>
    <span>Sugar Loom by Dana Welch</span>
    <svg class="owner-line__flag" viewBox="0 0 22 16" aria-hidden="true"><path d="M0 0 H22 L16 8 L22 16 H0 Z" fill="#e6a28f"/></svg>
  </div>
</section>

<section class="card card--back" aria-label="Card back">
  <div class="logo-ornament" role="img" aria-label="Peach flourish ornament with a tiered cake motif framing the brand name"></div>
  <div class="brand-name">Sugar Loom</div>
  <div class="tagline">HANDCRAFTED WITH LOVE</div>
  <div class="contacts">
    <div class="contacts__row">
      <span class="contact">
        <svg class="contact__icon" viewBox="0 0 16 16" aria-hidden="true"><path d="M1 6 Q8 0 15 6 L12 8 L10 6 H6 L4 8 Z M3 9 H13 L14 14 H2 Z" fill="#e6a28f"/></svg>
        (516) 555-0147
      </span>
      <span class="contact">
        <svg class="contact__icon" viewBox="0 0 16 16" aria-hidden="true"><rect x="1" y="3" width="14" height="10" fill="#e6a28f"/><path d="M1 3 L8 9 L15 3" fill="none" stroke="#fff" stroke-width="1.2"/></svg>
        hello@sugarloom.com
      </span>
      <span class="contact">
        <svg class="contact__icon" viewBox="0 0 16 16" aria-hidden="true"><circle cx="8" cy="8" r="6.5" fill="none" stroke="#e6a28f" stroke-width="1.5"/><ellipse cx="8" cy="8" rx="3" ry="6.5" fill="none" stroke="#e6a28f" stroke-width="1.2"/><path d="M1.5 8 H14.5" stroke="#e6a28f" stroke-width="1.2"/></svg>
        www.sugarloomsweets.com
      </span>
    </div>
    <div class="contacts__row">
      <span class="contact"><span class="contact__square"></span>sugarloomnyc</span>
      <span class="contact"><span class="contact__square"></span>sugarloom_ny</span>
    </div>
  </div>
</section>

</body>
</html>
```